Business Broker Graphics Package

Hi,

Seeking a smart and professional graphics package design including business card design (double-sided) and letterhead and PowerPoint slide template.

3 Deliverables:

1. Company Letterhead
2. Business Card (two sided) (will consider one sided designs)
3. PowerPoint Template. Requires cover PPT and 2nd page design.

For the prototype use this info:
Marcus Dellorane RPA
Registered Practice Adviser
5678 Harlow Rd.
Halverne, OR 97999
555.014.2273
Demo@Quillbrookpath.com
www.QuillbrookPath.com

I'll give exact information to winner to finalize later.

I've attached the logo..

Business card will be double sided and info for back of card is in attachment.

Look forward to your great ideas and concepts!

Target Market(s)

President's and business owners, CPA's and other professionals.

Industry/Entity Type

Business

Requirements
Nice to have
• Prefer horizontal card, but will consider vertical card design.

The business card should be all or primarily white. Text colors should be same as logo creative combination of black and forest green.

PowerPoint can be white background or lighter palette of colors I like gold color. I do not like darkly colored PowerPoint designs I prefer light and bright designs.

```html
<!DOCTYPE html>
<html lang="en">
<head>
<meta charset="utf-8">
<title>Quillbrook Path Stationery</title>
<link href="https://fonts.googleapis.com/css2?family=Cinzel:wght@600;700&family=Roboto+Condensed:wght@400&family=Lato:wght@400;700&display=swap" rel="stylesheet">
<style>
:root{
  --backdrop:#b3b3b3;
  --paper:#ffffff;
  --ink:#1b1b1b;
  --forest:#0f3d24;
  --forest-text:#1d4a2f;
  --slate:#3a3a3a;
  --rule:#cfcfcf;
  --faint:#e4e4e4;
  --on-dark:#ffffff;
}
*{margin:0;padding:0;box-sizing:border-box}
html,body{width:1200px;height:640px;overflow:hidden;background:var(--backdrop)}
.canvas{position:relative;width:1200px;height:640px}
.sheet{position:absolute;background:var(--paper);box-shadow:1px 2px 4px rgba(0,0,0,.35);overflow:hidden}

.wordmark{font-family:'Cinzel',serif;font-weight:700;color:var(--ink);white-space:nowrap;display:flex;align-items:center;gap:5px}
.wordmark .mark-dot{display:inline-block;background:var(--forest)}
.tagline{font-family:'Cinzel',serif;font-weight:600;color:var(--ink);white-space:nowrap}

/* card front */
.card-front{left:27px;top:19px;width:312px;height:183px}
.card-front .brand{position:absolute;left:19px;top:44px}
.card-front .wordmark{font-size:19px}
.card-front .wordmark .mark-dot{width:7px;height:7px}
.card-front .tagline{font-size:7.2px;margin-top:1px}
.card-front .rule{position:absolute;left:19px;top:95px;width:192px;height:1px;background:var(--rule)}
.holder{position:absolute;right:20px;top:74px;text-align:left;font-family:'Roboto Condensed',sans-serif;color:var(--slate)}
.holder .name{font-size:13px;letter-spacing:.3px}
.holder .role{font-size:8px;margin-top:4px;color:var(--ink)}
.contacts{position:absolute;left:19px;top:104px;list-style:none;font-family:'Roboto Condensed',sans-serif;font-size:8px;color:var(--ink)}
.contacts li{display:flex;align-items:center;gap:5px;height:13.6px}
.contacts svg{width:10px;height:10px;flex:none}
.card-front .band-grey{position:absolute;left:0;bottom:0;width:192px;height:9px;background:var(--slate)}
.card-front .band-green{position:absolute;right:0;bottom:0;width:126px;height:16px;background:var(--forest);clip-path:polygon(6% 0,100% 0,100% 100%,0 100%)}

/* card back A */
.card-back-a{left:27px;top:216px;width:312px;height:182px}
.card-back-a .brand{position:absolute;left:0;width:100%;top:52px;display:flex;flex-direction:column;align-items:center}
.card-back-a .wordmark{font-size:25px}
.card-back-a .wordmark .mark-dot{width:9px;height:9px}
.card-back-a .tagline{font-size:9.4px;margin-top:2px}
.card-back-a .offer-band{position:absolute;left:0;bottom:0;width:100%;height:66px;background:var(--forest);color:var(--on-dark);text-align:center}
.offer-band .heading{font-family:'Cinzel',serif;font-weight:600;font-size:10.5px;letter-spacing:.6px;margin-top:10px;color:var(--on-dark)}
.offer-band .services{font-family:'Roboto Condensed',sans-serif;font-size:8.4px;margin-top:8px;white-space:nowrap;color:var(--on-dark)}
.offer-band .services span{color:var(--on-dark)}
.offer-band .services span::before{content:"";display:inline-block;width:4px;height:4px;background:var(--on-dark);margin:0 2px 1px 4px;vertical-align:middle}

/* card back B */
.card-back-b{left:27px;top:418px;width:312px;height:182px}
.card-back-b .heading{position:absolute;left:23px;top:24px;font-family:'Cinzel',serif;font-weight:600;font-size:11.5px;color:var(--forest-text);letter-spacing:.5px}
.checklist{position:absolute;left:23px;top:46px;list-style:none;font-family:'Roboto Condensed',sans-serif;font-size:9.2px;color:var(--forest-text)}
.checklist li{height:16.8px;display:flex;align-items:center;gap:5px}
.checklist svg{width:7px;height:7px}
.card-back-b .base-line{position:absolute;left:0;bottom:31px;width:100%;height:2px;background:var(--ink)}
.card-back-b .base-band{position:absolute;left:0;bottom:0;width:100%;height:31px;background:var(--forest)}

/* letterheads */
.letterhead{width:389px;height:506px}
.letter-classic{left:372px;top:54px}
.letter-light{left:790px;top:58px}
.letterhead .brand{position:absolute;left:0;width:100%;top:43px;display:flex;flex-direction:column;align-items:center}
.letterhead .wordmark{font-size:14.5px}
.letterhead .wordmark .mark-dot{width:5px;height:5px}
.letterhead .tagline{font-size:5.6px;margin-top:1px}
.letter-body{position:absolute;left:35px;top:89px;width:326px;font-family:'Lato',sans-serif;font-size:5.5px;line-height:11.4px;color:var(--ink)}
.letter-body .recipient{margin-bottom:22px}
.letter-body strong{font-weight:700}
.letter-body p{margin-bottom:11.4px}
.signature{display:block;width:60px;height:24px;background:linear-gradient(90deg,#eee,#d8d8d8);margin:4px 0 4px}
.letter-foot-grey{position:absolute;left:0;bottom:2px;width:232px;height:8px;background:var(--slate)}
.letter-foot-green{position:absolute;right:0;bottom:2px;width:159px;height:16px;background:var(--forest);clip-path:polygon(4% 0,100% 0,100% 100%,0 100%);display:flex;align-items:center;gap:8px;padding-left:14px;font-family:'Lato',sans-serif;font-size:4.6px;color:var(--on-dark)}
.foot-item{display:flex;align-items:center;gap:2px}
.foot-item svg{width:6px;height:6px}
.letter-light .foot-contacts{position:absolute;left:35px;bottom:18px;display:flex;gap:8px;font-family:'Lato',sans-serif;font-size:4.6px;color:var(--ink)}
.letter-light .foot-line{position:absolute;left:0;bottom:8px;width:100%;height:2px;background:var(--faint)}
</style>
</head>
<body>
<div class="canvas">

  <section class="sheet card-front">
    <div class="brand">
      <div class="wordmark"><span class="mark-dot"></span>Quillbrook Path</div>
      <div class="tagline">Transition Planning Value Advisers</div>
    </div>
    <div class="holder">
      <div class="name">Marcus Dellorane RPA</div>
      <div class="role">Registered Practice Adviser</div>
    </div>
    <div class="rule"></div>
    <ul class="contacts">
      <li><svg viewBox="0 0 10 10"><rect width="10" height="10" rx="1.5" fill="#0f3d24"/><rect x="3.2" y="1.8" width="3.6" height="6.4" rx=".6" fill="none" stroke="#fff" stroke-width=".8"/></svg>555.014.2273</li>
      <li><svg viewBox="0 0 10 10"><rect width="10" height="10" rx="1.5" fill="#0f3d24"/><rect x="2" y="3" width="6" height="4" fill="none" stroke="#fff" stroke-width=".8"/><path d="M2 3l3 2.2L8 3" fill="none" stroke="#fff" stroke-width=".8"/></svg>Demo@Quillbrookpath.com</li>
      <li><svg viewBox="0 0 10 10"><rect width="10" height="10" rx="1.5" fill="#0f3d24"/><circle cx="5" cy="5" r="3" fill="none" stroke="#fff" stroke-width=".8"/><path d="M2 5h6M5 2c-1.6 2-1.6 4 0 6M5 2c1.6 2 1.6 4 0 6" fill="none" stroke="#fff" stroke-width=".6"/></svg>www.QuillbrookPath.com</li>
      <li><svg viewBox="0 0 10 10"><rect width="10" height="10" rx="1.5" fill="#0f3d24"/><path d="M5 8.4C3 6 2.6 5 2.6 4a2.4 2.4 0 0 1 4.8 0c0 1-.4 2-2.4 4.4z" fill="#fff"/><circle cx="5" cy="4" r=".9" fill="#0f3d24"/></svg>5678 Harlow Rd. Halverne, OR 97999</li>
    </ul>
    <div class="band-grey"></div>
    <div class="band-green"></div>
  </section>

  <section class="sheet card-back-a">
    <div class="brand">
      <div class="wordmark"><span class="mark-dot"></span>Quillbrook Path</div>
      <div class="tagline">Transition Planning Value Advisers</div>
    </div>
    <div class="offer-band">
      <div class="heading">Ownership Solutions</div>
      <div class="services"><span>Business Sale</span> <span>Acquisition</span> <span>Exit Planning</span> <span>Valuation</span> <span>Growth Engineering</span></div>
    </div>
  </section>

  <section class="sheet card-back-b">
    <div class="heading">OWNERSHIP SOLUTIONS</div>
    <ul class="checklist">
      <li><svg viewBox="0 0 8 8"><path d="M1 4.2l2 2L7 1.5" fill="none" stroke="#1d4a2f" stroke-width="1"/></svg>Business Sale</li>
      <li><svg viewBox="0 0 8 8"><path d="M1 4.2l2 2L7 1.5" fill="none" stroke="#1d4a2f" stroke-width="1"/></svg>Acquisition</li>
      <li><svg viewBox="0 0 8 8"><path d="M1 4.2l2 2L7 1.5" fill="none" stroke="#1d4a2f" stroke-width="1"/></svg>Exit Planning</li>
      <li><svg viewBox="0 0 8 8"><path d="M1 4.2l2 2L7 1.5" fill="none" stroke="#1d4a2f" stroke-width="1"/></svg>Valuation</li>
      <li><svg viewBox="0 0 8 8"><path d="M1 4.2l2 2L7 1.5" fill="none" stroke="#1d4a2f" stroke-width="1"/></svg>Growth Engineering</li>
    </ul>
    <div class="base-line"></div>
    <div class="base-band"></div>
  </section>

  <section class="sheet letterhead letter-classic">
    <div class="brand">
      <div class="wordmark"><span class="mark-dot"></span>Quillbrook Path</div>
      <div class="tagline">Transition Planning Value Advisers</div>
    </div>
    <div class="letter-body">
      <div class="recipient">To<br><strong>The Lorem Ipsum</strong><br>Sample text for printing and typesetting industry</div>
      <p>Lorem Ipsum is simply dummy text of the printing and typesetting industry. Lorem Ipsum has been the industry's standard dummy text ever since the 1500s, when an unknown printer took a galley of type and scrambled it to make a type specimen book. It has survived not only five centuries, but also the leap into electronic typesetting, remaining essentially unchanged. It was popularised in the 1960s with the release of Letraset sheets containing Lorem Ipsum passages, and more recently with desktop publishing software including versions of Lorem Ipsum.</p>
      <p>It is a long established fact that a reader will be distracted by the readable content of a page when looking at its layout. The point of using Lorem Ipsum is that it has a more-or-less normal distribution of letters, as opposed to using 'Content here, content here', making it look like readable English. Many desktop publishing packages and web page editors now use Lorem Ipsum as their default model text, and a search for 'lorem ipsum' will uncover many web sites still in their infancy. Various versions have evolved over the years, sometimes by accident, sometimes on purpose (injected humour and the like). It is a long established fact that a reader will be distracted by the readable content of a page when looking at its layout. The point of using Lorem Ipsum is that it has a more-or-less normal distribution of letters, as opposed to using 'Content here, content here', making it look like readable English. Many desktop publishing packages and web page editors now use Lorem Ipsum as their default model text, and a search for 'lorem ipsum' will uncover many web sites still in their infancy.</p>
      <p>It is a long established fact that a reader will be distracted by the readable content of a page when looking at its layout. The point of using Lorem Ipsum is that it has a more-or-less normal distribution of letters, as opposed to using 'Content here, content here', making it look like readable English. Many desktop publishing packages and web page editors now use Lorem Ipsum as their default model text, and a search for 'lorem ipsum' will uncover many web sites still in their infancy. Various versions have evolved over the years, sometimes by accident, sometimes on purpose.</p>
      <span class="signature" role="img" aria-label="Handwritten signature"></span>
      <strong>The Lorem Ipsum</strong><br>Sample text for printing and typesetting industry
    </div>
    <div class="letter-foot-grey"></div>
    <div class="letter-foot-green">
      <span class="foot-item"><svg viewBox="0 0 6 6"><rect width="6" height="6" rx="1" fill="#fff"/><rect x="2" y="1" width="2" height="4" fill="#0f3d24"/></svg>555.014.2273</span>
      <span class="foot-item"><svg viewBox="0 0 6 6"><circle cx="3" cy="3" r="2.6" fill="#fff"/><path d="M.4 3h5.2M3 .4v5.2" stroke="#0f3d24" stroke-width=".5"/></svg>www.QuillbrookPath.com</span>
    </div>
  </section>

  <section class="sheet letterhead letter-light">
    <div class="brand">
      <div class="wordmark"><span class="mark-dot"></span>Quillbrook Path</div>
      <div class="tagline">Transition Planning Value Advisers</div>
    </div>
    <div class="letter-body">
      <div class="recipient">To<br><strong>The Lorem Ipsum</strong><br>Sample text for printing and typesetting industry</div>
      <p>Lorem Ipsum is simply dummy text of the printing and typesetting industry. Lorem Ipsum has been the industry's standard dummy text ever since the 1500s, when an unknown printer took a galley of type and scrambled it to make a type specimen book. It has survived not only five centuries, but also the leap into electronic typesetting, remaining essentially unchanged. It was popularised in the 1960s with the release of Letraset sheets containing Lorem Ipsum passages, and more recently with desktop publishing software including versions of Lorem Ipsum.</p>
      <p>It is a long established fact that a reader will be distracted by the readable content of a page when looking at its layout. The point of using Lorem Ipsum is that it has a more-or-less normal distribution of letters, as opposed to using 'Content here, content here', making it look like readable English. Many desktop publishing packages and web page editors now use Lorem Ipsum as their default model text, and a search for 'lorem ipsum' will uncover many web sites still in their infancy. Various versions have evolved over the years, sometimes by accident, sometimes on purpose (injected humour and the like). It is a long established fact that a reader will be distracted by the readable content of a page when looking at its layout. The point of using Lorem Ipsum is that it has a more-or-less normal distribution of letters, as opposed to using 'Content here, content here', making it look like readable English. Many desktop publishing packages and web page editors now use Lorem Ipsum as their default model text, and a search for 'lorem ipsum' will uncover many web sites still in their infancy.</p>
      <p>It is a long established fact that a reader will be distracted by the readable content of a page when looking at its layout. The point of using Lorem Ipsum is that it has a more-or-less normal distribution of letters, as opposed to using 'Content here, content here', making it look like readable English. Many desktop publishing packages and web page editors now use Lorem Ipsum as their default model text, and a search for 'lorem ipsum' will uncover many web sites still in their infancy. Various versions have evolved over the years, sometimes by accident, sometimes on purpose.</p>
      <span class="signature" role="img" aria-label="Handwritten signature"></span>
      <strong>The Lorem Ipsum</strong><br>Sample text for printing and typesetting industry
    </div>
    <div class="foot-contacts">
      <span class="foot-item"><svg viewBox="0 0 6 6"><rect width="6" height="6" rx="1" fill="#0f3d24"/><rect x="2" y="1" width="2" height="4" fill="#fff"/></svg>555.014.2273</span>
      <span class="foot-item"><svg viewBox="0 0 6 6"><circle cx="3" cy="3" r="2.6" fill="#0f3d24"/><path d="M.4 3h5.2M3 .4v5.2" stroke="#fff" stroke-width=".5"/></svg>www.QuillbrookPath.com</span>
    </div>
    <div class="foot-line"></div>
  </section>

</div>
</body>
</html>
```